Modernize Website: marcusfellwright.net

I am a novelist with an older-generation website at: marcusfellwright.net.

I am hoping to refresh this outdated website with a new, responsive redesign. I would prefer to host the code myself, and edit using Adobe Dreamweaver. So I’m not looking to use a hosted site builder like Plexo. Nor am I looking to use a CMS like Pagecraft.

In order to simplify the old site, there are a number of sections I’ll be looking to remove during this redesign. These are shown in the "MF Site Redesign" attachment. I can also provide imagery for new content (another book series in addition to the existing one), as well as higher-resolution imagery (if needed) of the old content.

Happy to answer any further questions.
Updates

I've uploaded a ZIP file containing high-res artwork associated with the new trilogy of books.

Target Market(s)

Readers of epic fantasy novels such as H.W.B. Castellane's THE WARDEN OF THE VALES, Harold P.Q. Ventris's A CROWN OF ASH AND RAIN, Victor Halloway's THE GATE OF STARS, or Dennis Vale's BLADE OF MERIVANE.

Industry/Entity Type

Entertainment

Coding

Coded - Design and coding required

Number of Pages Required

5+ page

Font styles to use
Serif
Decorative

Colors

Designer to choose colors to be used in the design.

Requirements
Must have
• I'm looking for a responsive design that displays nicely on both mobile and desktop devices. Existing site contains multiple pages, but these can obviously be combined into fewer pages (or even one) by divisions such as tabs, sections, and/or modal windows. See marcusfellwright.net for current content and "MF Site Redesign" attachment for content to be removed at this time.
Nice to have
• The ability to fulfill orders of autographed books directly from the website. I currently use Coinlo to do this, but it would be nice to incorporate a more comprehensive merchant service at a reasonable rate.
Should not have
• I'd like to host and control the site code myself. So please don't use a hosted web builder like Plexo, or a cloud-based CMS like Pagecraft.

```html
<!DOCTYPE html>
<html lang="en">
<head>
<meta charset="utf-8">
<title>Marcus Fellwright — Novels — Buy Online</title>
<link rel="stylesheet" href="https://fonts.googleapis.com/css2?family=Cinzel:wght@400;700&family=Crimson+Text:wght@400;600&family=Roboto:wght@400;500;700&display=swap">
<style>
:root{
  --black:#000;
  --night:#121015;
  --red:#d4001c;
  --red-dark:#8a0010;
  --white:#fff;
  --grey:#cfcfcf;
  --ember:#e0501a;
}
*{margin:0;padding:0;box-sizing:border-box}
html,body{width:1200px;height:2384px;overflow:hidden;background:var(--night)}
body{position:relative;font-family:"Roboto",Arial,sans-serif;color:var(--white)}
.abs{position:absolute}

/* header */
.site-header{left:0;top:0;width:1200px;height:121px;background:var(--black);z-index:5}
.brand{left:100px;top:30px;font-family:"Cinzel",serif;font-size:24px;line-height:26px;color:var(--grey);letter-spacing:1px}
.brand small{display:block;font-size:11px;line-height:16px;color:var(--red);letter-spacing:2px;margin-left:70px}
.main-nav{left:529px;top:64px;display:flex;font-size:15px;font-weight:500}
.main-nav a{color:var(--white);text-decoration:none;margin-right:25px;display:flex;align-items:center;gap:4px}
.caret{width:9px;height:6px}
.nav-pin{left:631px;top:0;width:3px;height:62px;background:linear-gradient(#ff2a3a,transparent)}
.login{left:992px;top:57px;width:108px;height:35px;border-radius:18px;background:linear-gradient(var(--red),var(--red-dark));display:flex;align-items:center;justify-content:center;gap:6px;font-size:14px;font-weight:700}
.dropdown{left:601px;top:121px;width:155px;height:194px;background:var(--black);z-index:6;font-size:14px;font-weight:500}
.dropdown li{list-style:none;position:absolute;left:0;width:155px;padding-left:21px;height:24px;line-height:24px}
.dropdown .active{background:linear-gradient(#ff1a2e,var(--red-dark));height:37px;line-height:37px}

/* hero */
.hero{left:0;top:121px;width:1200px;height:560px;
  background:
    radial-gradient(ellipse 260px 380px at 70px 250px,rgba(120,112,100,.75),transparent 70%),
    radial-gradient(ellipse 380px 330px at 900px 230px,rgba(70,70,52,.85),transparent 70%),
    radial-gradient(ellipse 520px 240px at 560px 120px,rgba(215,190,185,.7),transparent 70%),
    radial-gradient(ellipse 300px 120px at 520px 520px,rgba(110,90,80,.6),transparent 70%),
    linear-gradient(180deg,#5c4a58 0%,#7a6670 35%,#45373f 65%,var(--night) 100%)}
.hero-title{left:108px;top:290px;font-family:"Cinzel",serif;font-weight:700;font-size:94px;line-height:110px;color:var(--white);text-shadow:0 0 16px var(--red),0 0 6px var(--red)}

.backdrop{left:0;top:681px;width:1200px;height:1324px;
  background:
    radial-gradient(ellipse 160px 60px at 0 1050px,rgba(224,80,26,.55),transparent 70%),
    radial-gradient(ellipse 140px 50px at 1200px 1400px,rgba(255,140,40,.6),transparent 70%),
    radial-gradient(ellipse 130px 50px at 0 1330px,rgba(224,80,26,.4),transparent 70%),
    radial-gradient(ellipse 700px 160px at 600px 1240px,rgba(110,30,12,.55),transparent 70%),
    linear-gradient(180deg,var(--night) 0%,#17121a 40%,#2a1710 80%,#1b0e0a 100%);
  background-position:0 -681px;background-size:1200px 2005px}
.section-title{left:0;top:685px;width:1200px;text-align:center;font-family:"Cinzel",serif;font-weight:700;font-size:58px;line-height:66px}

/* gallery */
.gallery{top:1600px;width:308px;height:259px}
.g1{left:99px;background:radial-gradient(ellipse at 30% 40%,#a07a64,transparent 55%),radial-gradient(ellipse at 80% 70%,#d2581a,transparent 45%),linear-gradient(135deg,#3a2a24,#1e1410)}
.g2{left:445px;background:radial-gradient(ellipse at 45% 60%,#8a1f24,transparent 50%),radial-gradient(ellipse at 20% 30%,#8a8aa0,transparent 50%),linear-gradient(135deg,#55505e,#2a2226)}
.g3{left:793px;background:radial-gradient(ellipse at 35% 40%,#4e4a4c,transparent 50%),radial-gradient(ellipse at 75% 55%,#5a5658,transparent 45%),linear-gradient(135deg,#262426,#151415)}

/* modal */
.modal{left:90px;top:775px;width:1020px;height:906px;background:var(--black);border:3px solid var(--red);z-index:3;text-align:center}
.close{left:1048px;top:770px;width:64px;height:64px;border-radius:50%;background:var(--red);z-index:4;display:flex;align-items:center;justify-content:center}
.modal-title{position:absolute;left:0;width:100%;top:88px;font-family:"Cinzel",serif;font-size:32px;font-weight:700;line-height:44px}
.intro{position:absolute;left:100px;width:815px;top:175px;font-size:12.5px;line-height:25px}
.note{position:absolute;left:0;width:100%;top:253px;font-size:12px;line-height:18px}
.series{position:absolute;left:0;width:100%;top:322px;font-family:"Cinzel",serif;font-size:26px;font-weight:400;line-height:36px}
.book{position:absolute;left:0;width:100%;top:385px;font-family:"Crimson Text",serif;font-weight:600;font-size:22px;line-height:28px}
.card{position:absolute;top:441px;width:220px;height:349px;border:2px solid var(--grey)}
.format{margin-top:20px;font-family:"Crimson Text",serif;font-weight:600;font-size:21px;line-height:26px;color:var(--red)}
.cover{position:relative;width:130px;height:200px;margin:10px auto 0;padding-top:12px;font-family:"Cinzel",serif;line-height:1}
.cover .author{font-size:19px;color:#e4d8d0}
.cover .title{position:absolute;left:0;width:100%;bottom:14px;font-size:20px;color:#f0e6da}
.cv1{background:radial-gradient(ellipse at 50% 70%,#b43c26,transparent 30%),radial-gradient(ellipse at 50% 55%,#6f8290,transparent 60%),linear-gradient(#44525a,#1c272d)}
.cv1 .title{color:#c01a1a}
.cv2{background:radial-gradient(ellipse at 50% 50%,#ff8a2a,transparent 30%),linear-gradient(#b22016 0%,#7a120c 40%,#30120a 75%,#9a1a12 76%,#8a140e 100%)}
.cv3{background:radial-gradient(ellipse at 50% 65%,#f0a040,transparent 35%),linear-gradient(#a8281a,#5a0e08 60%,#2a0604)}
.isbn{margin-top:11px;font-family:"Crimson Text",serif;font-size:17px;line-height:22px}
.vendors{margin-top:9px;display:flex;justify-content:center;gap:9px}
.vendors span{width:14px;height:14px;display:block;border:1px solid #666}
.v-brown{background:#7a5a36}.v-green{background:#3c6a3e}.v-blue{background:#2a5aa8}.v-red{background:#c81e2a}.v-pink{background:#c8288a}.v-grey{background:#d8d8d8}
.arrow{position:absolute;top:599px}

/* footer */
.site-footer{left:0;top:2005px;width:1200px;height:379px;background:var(--black);text-align:center}
.footer-brand{position:absolute;left:0;width:100%;top:72px;font-family:"Cinzel",serif;font-size:22px;line-height:26px;color:var(--grey)}
.social{position:absolute;left:513px;top:169px;display:flex;gap:11px}
.social span{width:51px;height:51px;border-radius:50%;background:var(--white);color:var(--red);display:flex;align-items:center;justify-content:center;font-size:11px;font-weight:700}
.footer-nav{position:absolute;left:0;width:100%;top:262px;font-size:14px}
.footer-nav span{margin:0 18px}
.legal{position:absolute;left:0;width:100%;top:309px;font-size:13px}
.legal span{margin:0 12px}
</style>
</head>
<body>
<header class="abs site-header">
  <div class="abs brand">MARCUS<br>FELLWRIGHT<small>The Legend of Veyrath</small></div>
  <nav class="abs main-nav">
    <a>HOME</a>
    <a>NOVELS <svg class="caret" viewBox="0 0 9 6"><path d="M1 1l3.5 3.5L8 1" stroke="#fff" stroke-width="1.5" fill="none"/></svg></a>
    <a>WORLD <svg class="caret" viewBox="0 0 9 6"><path d="M1 1l3.5 3.5L8 1" stroke="#fff" stroke-width="1.5" fill="none"/></svg></a>
    <a>AUTHOR <svg class="caret" viewBox="0 0 9 6"><path d="M1 1l3.5 3.5L8 1" stroke="#fff" stroke-width="1.5" fill="none"/></svg></a>
    <a>CONTACT</a>
  </nav>
  <div class="abs nav-pin"></div>
  <div class="abs login"><svg width="11" height="13" viewBox="0 0 11 13"><rect x="0" y="5" width="11" height="8" rx="1" fill="#fff"/><path d="M2.5 5V3.5a3 3 0 016 0V5" stroke="#fff" stroke-width="1.6" fill="none"/></svg>LOGIN</div>
</header>
<ul class="abs dropdown">
  <li style="top:12px">Summaries</li>
  <li style="top:39px">Excerpts</li>
  <li style="top:66px">Reviews</li>
  <li class="active" style="top:102px">Buy Online</li>
  <li style="top:156px">Signed Copies</li>
</ul>

<div class="abs hero" role="img" aria-label="Fantasy scene of a dragon above a ruined tower and a lone figure under stormy skies"></div>
<h1 class="abs hero-title">NOVELS</h1>

<div class="abs backdrop"></div>
<h2 class="abs section-title">BUY ONLINE</h2>

<div class="abs gallery g1" role="img" aria-label="Artwork of a clawed creature amid fire"></div>
<div class="abs gallery g2" role="img" aria-label="Artwork of a red horned beast in a fiery field"></div>
<div class="abs gallery g3" role="img" aria-label="Artwork of armoured warriors in battle"></div>

<section class="abs modal">
  <h2 class="modal-title">THE ONYX SEAL</h2>
  <p class="intro">In addition to being available at fine bookstores everywhere, the following titles may be purchased from a variety of online sources. Ordering shortcuts have been provided for each title and format below. Simply locate the desired book and click on the vender button of choice.</p>
  <p class="note">Note: To purchase autographed copies, visit the Signed Copies page instead.</p>
  <h3 class="series">THE LEGEND OF VEYRATH</h3>
  <h4 class="book">The Scarlet Blade</h4>

  <svg class="arrow" style="left:60px" width="24" height="40" viewBox="0 0 24 40"><path d="M20 4L6 20l14 16" stroke="#fff" stroke-width="5" fill="none"/></svg>
  <div class="card" style="left:125px">
    <p class="format">Hardcover</p>
    <div class="cover cv1" role="img" aria-label="Book cover for The Scarlet Blade"><div class="author">MARCUS<br>FELLWRIGHT</div><div class="title">SCARLET<br>BLADE</div></div>
    <p class="isbn">ISBN: 0123456781</p>
    <div class="vendors"><span class="v-brown"></span><span class="v-green"></span></div>
  </div>
  <div class="card" style="left:398px">
    <p class="format">Paperback</p>
    <div class="cover cv2" role="img" aria-label="Book cover for The Onyx Seal"><div class="author">MARCUS<br>FELLWRIGHT</div><div class="title">THE<br>ONYX SEAL</div></div>
    <p class="isbn">ISBN: 0123456799</p>
    <div class="vendors"><span class="v-brown"></span><span class="v-green"></span><span class="v-blue"></span><span class="v-red"></span><span class="v-grey"></span></div>
  </div>
  <div class="card" style="left:671px">
    <p class="format">Digital (eBook)</p>
    <div class="cover cv3" role="img" aria-label="Book cover for The Onyx Seal ebook"><div class="author">MARCUS<br>FELLWRIGHT</div><div class="title">ONYX<br>SEAL</div></div>
    <p class="isbn">ISBN: (by Format)</p>
    <div class="vendors"><span class="v-brown"></span><span class="v-green"></span><span class="v-blue"></span><span class="v-grey"></span><span class="v-pink"></span></div>
  </div>
  <svg class="arrow" style="left:932px" width="24" height="40" viewBox="0 0 24 40"><path d="M4 4l14 16L4 36" stroke="#fff" stroke-width="5" fill="none"/></svg>
</section>
<div class="abs close"><svg width="24" height="24" viewBox="0 0 24 24"><path d="M4 4l16 16M20 4L4 20" stroke="#fff" stroke-width="5"/></svg></div>

<footer class="abs site-footer">
  <div class="footer-brand">MARCUS FELLWRIGHT</div>
  <div class="social">
    <span>Folio</span><span>Chirp</span>
    <span><svg width="22" height="16" viewBox="0 0 22 16"><rect x="1" y="1" width="20" height="14" rx="2" fill="none" stroke="#d4001c" stroke-width="2"/><path d="M1 2l10 7 10-7" fill="none" stroke="#d4001c" stroke-width="2"/></svg></span>
  </div>
  <nav class="footer-nav"><span>Home</span>|<span>Novels</span>|<span>World</span>|<span>Author</span>|<span>Contact</span></nav>
  <p class="legal"><span>© Copyright 2018 Marcus Fellwright. All Rights Reserved</span>|<span>Terms of Use</span>|<span>Privacy Policy.</span></p>
</footer>
</body>
</html>
```